freshen up existing wordpress site

We wish to re-implement our current wordpress website www.vornimax.com/web2.

The content, structure and menus of the website should remain the same, but style updated to a more fresh/contemporary layout. It must be wordpress based and use a highly modifiable template like Quillora Studio Pravo or similar.

Permalinks must be exactly as the old ones.

Landing page must contain a slider for images and movies, plus a little text. There is no requirement for a tab-style as seem on the current website.

The final result shall be transferred to a fresh multisite installation of wordpress, we will provide login for access later. If another method is better/more preferred, please comment and we can take it from there.

The two graphics on http://vornimax.com/web2/gridmarshal-product-details/ should be re-done to look more 'clean and professional' and look less powerpoint'ish. We will need the vectorfiles for edits later on. Color scheme is open, whatever matches with the the website style.

We work in a engineering-heavy B2B environment, so slightly conservative/boring styles; no 'pop smartness'. competitors websites looks like this:
- http://www.lumivex.com/
- http://www.corbantix.com/
- https://www.ostrivel.com/products/ic_nanometer_design/
- https://www.quendor-da.com/

Website background should be white for easy image implementation. Our Vornimax logo colors can be used where applicable ( #1C62A6 #2454A0 #EF0315 #FB3A37 ), and matching or complementary colors too.

Use Sans Serif fonts like googles or something like http://www.glyphbarrow.com/fonts/noto-sans .

Target Market(s)

semiconductor industry

Number of Pages Required

5+ page

Font styles to use
Sans Serif

Requirements
Must have
• see above
Nice to have
• see above
Should not have
• not defined.

```html
<!DOCTYPE html>
<html lang="en">
<head>
<meta charset="utf-8">
<title>Vornimax – Home</title>
<link rel="stylesheet" href="https://fonts.googleapis.com/css2?family=Noto+Sans:wght@400;700&display=swap">
<style>
:root{
  --blue:#2454A0;
  --blue-mid:#1C62A6;
  --red:#FB3A37;
  --red-deep:#EF0315;
  --ink:#333;
  --muted:#666;
  --line:#e6e6e6;
  --bar:#ececec;
  --white:#fff;
}
*{box-sizing:border-box;margin:0;padding:0}
html,body{width:926px;height:1200px;overflow:hidden}
body{font-family:"Noto Sans",Arial,sans-serif;background:var(--white);color:var(--ink);position:relative}
.site-header{height:63px;border-top:3px solid var(--blue);position:relative}
.brand{position:absolute;left:124px;top:15px;display:flex;align-items:center;gap:6px;text-decoration:none}
.brand-mark{width:22px;height:22px;background:var(--red)}
.brand-name{font-weight:700;font-size:29px;color:var(--blue);letter-spacing:-.5px;line-height:1}
.main-nav{position:absolute;left:392px;top:27px;display:flex;font-size:9px;font-weight:700}
.main-nav a{color:var(--blue);text-decoration:none;margin-right:38px}
.main-nav a.active{color:var(--red)}
.search-btn{position:absolute;left:774px;top:20px;width:28px;height:28px;border-radius:50%;background:var(--red)}
.hero{position:absolute;top:64px;left:0;width:926px;height:347px;
  background:radial-gradient(ellipse at 25% 40%,#0e2c5a 0%,#1b4f95 35%,transparent 60%),linear-gradient(110deg,#2a6fc0 0%,#3f8ad8 45%,#2b6bc0 75%,#1e57a8 100%)}
.hero-copy{position:absolute;right:125px;top:114px;text-align:right;color:var(--white)}
.hero-title{font-weight:700;font-size:31px;line-height:1.1}
.hero-sub{font-weight:400;font-size:24px;line-height:1.3}
.hero-sub.small{font-size:22px}
.slider-dots{position:absolute;left:439px;top:320px;display:flex;gap:3px}
.slider-dots span{width:10px;height:10px;border-radius:50%;background:var(--white)}
.slider-dots span.on{background:var(--red)}
.features{position:absolute;top:434px;left:124px;width:677px;display:flex;justify-content:space-between}
.feature{width:215px;box-shadow:0 8px 8px -6px rgba(0,0,0,.25)}
.feature-img{height:103px}
.feature-img.suit{background:linear-gradient(90deg,#1b1b1b,#2a4d6a 60%,#1f6b8a)}
.feature-img.chip{background:linear-gradient(120deg,#1a3a1a,#6aa82a 45%,#d6b52a 75%,#3a2f10)}
.feature-img.team{background:linear-gradient(90deg,#d8c8c8,#b9b7b7 50%,#8a9aa8)}
.feature-label{height:29px;background:var(--blue);color:var(--white);font-size:10px;font-weight:700;display:flex;align-items:center;justify-content:space-between;padding:0 10px}
.feature-label.red{background:var(--red)}
.feature-label i{width:8px;height:8px;border-radius:50%;background:var(--white);display:block}
.divider{position:absolute;top:595px;left:124px;width:677px;border-top:1px solid var(--line)}
.panel{position:absolute;border:1px solid var(--line)}
.panel-head{height:29px;background:var(--bar);border-left:3px solid var(--red);font-size:10px;font-weight:700;display:flex;align-items:center;padding-left:8px;color:var(--ink)}
.about{left:124px;top:620px;width:215px;height:300px}
.about-img{margin:12px 11px 0;height:108px;border:2px solid #ddd;background:linear-gradient(160deg,#1c8a3a,#4f6a2a 45%,#b33a1a 75%,#e0402a)}
.about h3{font-weight:400;font-size:11.5px;color:var(--red);margin:10px 12px 9px}
.about p{font-size:8px;line-height:1.65;color:var(--muted);margin:0 12px;text-align:justify}
.btn{display:inline-block;margin:12px 12px 0;background:var(--red);color:var(--white);font-size:8px;padding:8px 12px;text-decoration:none}
.events{left:356px;top:620px;width:215px;height:300px}
.event{display:flex;gap:11px;padding:12px 12px 0;height:67px;border-bottom:1px solid var(--line)}
.event:last-child{border-bottom:0}
.date{width:46px;height:45px;flex:none;background:var(--blue);color:var(--white);text-align:center;padding-top:6px;font-size:8px;line-height:1}
.date b{display:block;font-weight:400;font-size:13px;margin-top:2px}
.event h4{font-weight:400;font-size:9px;color:var(--red);margin-bottom:7px}
.event p{font-size:8px;color:var(--muted);line-height:1.55}
.news{left:586px;top:620px;width:215px;height:300px}
.tabs{display:flex;height:29px;background:var(--bar);font-size:10px;font-weight:700}
.tabs span{display:flex;align-items:center;padding:0 9px;color:var(--muted)}
.tabs span.on{background:var(--red);color:var(--white)}
.news-item{padding:10px 15px 0;height:81px;border-bottom:1px solid var(--line)}
.news-item h4{font-weight:400;font-size:9px;color:var(--blue);margin-bottom:7px}
.news-item p{font-size:8px;line-height:1.55;color:var(--muted)}
.stamp{font-size:7px;color:var(--red);margin-top:5px;display:flex;align-items:center;gap:2px}
.stamp::before{content:"";width:6px;height:6px;border:1px solid var(--red);display:block}
.more{font-size:7.5px;color:var(--red);padding:10px 15px;display:block;text-decoration:none}
.webinars{left:124px;top:940px;width:677px;height:183px}
.webinar-row{display:flex;padding:19px 10px 0}
.webinar{display:flex;width:338px;gap:12px}
.webinar-img{width:143px;height:115px;border:2px solid #ddd;flex:none}
.webinar-img.coil{background:linear-gradient(135deg,#d9a090,#c0503a 50%,#e03a3a)}
.webinar-img.solar{background:linear-gradient(160deg,#dfe8f0,#3a58a8 45%,#1e3478)}
.webinar h4{font-weight:400;font-size:9px;color:var(--blue);margin:6px 0 7px}
.webinar p{font-size:8px;line-height:1.7;color:var(--muted);text-align:justify;width:162px}
.site-footer{position:absolute;left:0;top:1146px;width:926px;height:54px;background:var(--blue)}
.social{position:absolute;left:126px;top:16px;display:flex;gap:3px}
.social span{width:22px;height:22px;border-radius:50%;border:1.5px solid var(--white)}
.copyright{position:absolute;left:499px;top:21px;font-size:8px;color:var(--white)}
.footer-brand{position:absolute;left:702px;top:13px;display:flex;align-items:center;gap:4px}
.footer-brand .brand-mark{width:14px;height:14px;background:#c8d3e6}
.footer-brand .brand-name{font-size:19px;color:#c8d3e6}
</style>
</head>
<body>
<header class="site-header">
  <a class="brand" href="#"><span class="brand-mark"></span><span class="brand-name">vornimax</span></a>
  <nav class="main-nav">
    <a class="active" href="#">HOME</a><a href="#">PRODUCT »</a><a href="#">COMPANY »</a><a href="#">NEWS</a><a href="#">CONTACT US</a>
  </nav>
  <span class="search-btn"><svg width="28" height="28" viewBox="0 0 28 28"><circle cx="13" cy="13" r="3" fill="none" stroke="#fff" stroke-width="1.5"/><line x1="15" y1="15" x2="17" y2="17" stroke="#fff" stroke-width="1.5"/></svg></span>
</header>

<section class="hero" role="img" aria-label="Close-up of a microprocessor chip on a blue circuit board">
  <div class="hero-copy">
    <div class="hero-title">Grid Marshal 4</div>
    <div class="hero-sub">Reduce Dynamic Voltage</div>
    <div class="hero-sub small">Drop And in-Rush Current</div>
  </div>
  <div class="slider-dots"><span></span><span></span><span class="on"></span><span></span></div>
</section>

<section class="features">
  <a class="feature"><div class="feature-img suit" role="img" aria-label="Businessman in suit beside a digital circuit overlay"></div><div class="feature-label red">GRID MARSHAL<i></i></div></a>
  <a class="feature"><div class="feature-img chip" role="img" aria-label="Microchip on a glowing green and yellow circuit board"></div><div class="feature-label">PRODUCT DETAILS<i></i></div></a>
  <a class="feature"><div class="feature-img team" role="img" aria-label="Engineers examining a circuit board at a table"></div><div class="feature-label">VIDEO TESTIMONIALS<i></i></div></a>
</section>

<div class="divider"></div>

<section class="panel about">
  <div class="panel-head">ABOUT US</div>
  <div class="about-img" role="img" aria-label="Silicon wafer grid lit in green and red"></div>
  <h3>Sed ut perspiciatis unde omnis iste</h3>
  <p>Sed ut perspiciatis unde omnis iste natus error sit voluptatem accusantium doloremque lauda ntium, totam rem aperiam, eaque ipsa quae ab illo inventore veritatis et quasi architecto Sed ut perspiciatis unde omnis iste natus</p>
  <a class="btn" href="#">READ MORE</a>
</section>

<section class="panel events">
  <div class="panel-head">EVENT CALENDAR</div>
  <div class="event"><div class="date">Jan 23<b>2016</b></div><div><h4>Sed ut perspiciatis unde</h4><p>Sed ut perspiciatis unde omnis te natus error sit voluptatem</p></div></div>
  <div class="event"><div class="date">Jan 23<b>2016</b></div><div><h4>Sed ut perspiciatis unde</h4><p>Sed ut perspiciatis unde omnis te natus error sit voluptatem</p></div></div>
  <div class="event"><div class="date">Jan 23<b>2016</b></div><div><h4>Sed ut perspiciatis unde</h4><p>Sed ut perspiciatis unde omnis te natus error sit voluptatem</p></div></div>
  <div class="event"><div class="date">Jan 23<b>2016</b></div><div><h4>Sed ut perspiciatis unde</h4><p>Sed ut perspiciatis unde omnis te natus error sit voluptatem</p></div></div>
</section>

<section class="panel news">
  <div class="tabs"><span class="on">LATEST NEWS</span><span>BLOG NEWS</span></div>
  <div class="news-item"><h4>Sed ut perspiciatis unde omnis iste na</h4><p>Sed ut perspiciatis unde omnis iste natus error sit voluptatem accusantium doloremque</p><div class="stamp">Jan 23 2016</div></div>
  <div class="news-item"><h4>Sed ut perspiciatis unde omnis iste na</h4><p>Sed ut perspiciatis unde omnis iste natus error sit voluptatem accusantium doloremque</p><div class="stamp">Jan 23 2016</div></div>
  <div class="news-item" style="border-bottom:0;height:70px"><h4>Sed ut perspiciatis unde omnis iste na</h4><p>Sed ut perspiciatis unde omnis iste natus error sit voluptatem accusantium doloremque</p><div class="stamp">Jan 23 2016</div></div>
  <a class="more" href="#">Read More News</a>
</section>

<section class="panel webinars">
  <div class="panel-head">EVENTS AND WEBINARS</div>
  <div class="webinar-row">
    <article class="webinar"><div class="webinar-img coil" role="img" aria-label="Copper coil inductor on a red circuit board"></div><div><h4>Sed ut perspiciatis unde omnis iste na</h4><p>Sed ut perspiciatis unde omnis iste natus error sit voluptatem accu santi umolorem qb illo inventore veritatis et quasi archi-tecto beatae vitae dicta sunt explicabo. Nemo enim ipsam voluptatem</p><div class="stamp">Jan 23 2016</div></div></article>
    <article class="webinar"><div class="webinar-img solar" role="img" aria-label="Solar panels under a pale sky"></div><div><h4>Sed ut perspiciatis unde omnis iste na</h4><p>Sed ut perspiciatis unde omnis iste natus error sit voluptatem accu santi umolorem qb illo inventore veritatis et quasi archi-tecto beatae vitae dicta sunt explicabo. Nemo enim ipsam voluptatem</p><div class="stamp">Jan 23 2016</div></div></article>
  </div>
</section>

<footer class="site-footer">
  <div class="social" aria-label="Social links"><span></span><span></span><span></span><span></span></div>
  <div class="copyright">© Copyright 2016 Vornimax A/S. All rights reserved.</div>
  <div class="footer-brand"><span class="brand-mark"></span><span class="brand-name">vornimax</span></div>
</footer>
</body>
</html>
```